Luxury Tours Design

We are “Amber Coachline” a Chauffeur Company based in Maidenhead, Berkshire. Our website is - ambercoachline.co.uk which will give you an insite into the Company.
Our clients consist of luxurious Hotels, large Corporate Companies along with private UHNW clients.
We have a fleet of Valtrane E, S and V Class vehicles along with 16 Seater Executive Coaches so we can accommodate single travellers, couples, friends, families and groups.
We would like an A5 (or slightly larger) double sided colour leaflet designed to promote our Tours in our local and surrounding areas.
The information below is some indication as to what we would like.
On the front we would like:-
Amber Coachline “Signature Tour” This will be our main promoting Tour
Slogan “Amber Coachline….ever at your service”
Tour will include:-
Visiting the historic town of Windsor, Hollenby Castle, St Aldric’s Chapel and Regal Pemberly Shopping Arcade.
Then onto Eton (Dunmere College) and a lovely view of the River Thames along with an array of Antique Shops in the quaint streets.
Bray Village (Heron Isle), renowed for it’s Brevard Star Restaurants and pubs.
Through picturesque Cookham along to Marlow for some shopping in the boutique shops, small listed buildings and beautiful places for refreshments, along with stunning views of the River Thames form Ashcombe Bridge.
This will be our main tour we offer but again this is flexible. This aims to be around 4-5 hours.
On the front, a picture of Hollenby castle maybe a large picture with writing over the top, or a separate photo….. a couple of photos attached or something similar.
On the back of the leaflet:-
We offer London based tours including:-
Belvards, Larkmoor Park, Ravensholt Palace, Corringdale Palace, Pellington Square, Turning of the Sentries, Keep of Ardmoor, Tall Tom, Glenmoreton Abbey to name a few! Or maybe London by night with a show or restaurant.
On the back a picture of Corringdale Palace…a couple of picture are also attached or again something similar.
Other Tours provided:-
Ridgewell Court Palace, Oxford and Corvane Palace, Ashmarrow Ring and Bath, The Cotswolds, Stratford and Penlow Castle, Quillford Shopping Village.
Also bespoke Tours can be arranged. We can personalise any tour to your requirements.
Experienced friendly Chauffeur’s, no request too big or small.
Please call us on 01632 960417 or email us sales@ambercoachline.co.uk
Please can you do an initial design including the above information.
Look forward to hearing from you.
Kind regards
Please visit https://www.hartleyprivatedrives.co.uk/ to get an idea of the tours of London to go on the back.
Prices will follow to be added after design and layout has been done.
Our AC logo is available on www.ambercoachline.co.uk
We want text to be editable and also for the design to have a luxury feel.
Chauffeur

```html
<!DOCTYPE html>
<html lang="en">
<head>
<meta charset="utf-8">
<title>Amber Coachline – Tours Leaflet</title>
<link href="https://fonts.googleapis.com/css2?family=Great+Vibes&family=Poppins:ital,wght@0,300;0,400;0,500;0,600;1,400;1,600;1,700&display=swap" rel="stylesheet">
<style>
:root{
  --backdrop:#a89f9f;
  --ink-dark:#4a4330;
  --ink-text:#2a2a28;
  --panel-dark:#2a2920;
  --panel-olive:rgba(118,106,66,.78);
  --gold:#d4b84a;
  --gold-deep:#9b8a3c;
  --white:#ffffff;
}
*{margin:0;padding:0;box-sizing:border-box}
html,body{width:800px;height:1200px;overflow:hidden}
body{background:var(--backdrop);font-family:'Poppins',sans-serif;position:relative}
.leaflet{position:absolute;left:211px;width:378px;height:536px;background:var(--panel-dark);overflow:hidden}
.leaflet--front{top:45px}
.leaflet--back{top:619px}
.photo{position:absolute;left:0;top:0;width:100%}
.photo--castle{height:320px;background:linear-gradient(180deg,#cdd9e2 0%,#e6c5bb 14%,#ef9f92 24%,#c9a99a 30%,#8d8f72 36%,#52702d 46%,#40602a 60%,#33412a 78%,#2a2920 100%)}
.photo--palace{height:345px;background:linear-gradient(180deg,#c9dae6 0%,#d8d5da 20%,#efb2a4 40%,#f0a08f 48%,#cfcac2 55%,#b7b3aa 68%,#d9c33a 74%,#c7372b 82%,#b9a83a 88%,#4a4a30 95%,#2a2920 100%)}
.script-title{position:absolute;left:0;width:100%;text-align:center;font-family:'Great Vibes',cursive;color:var(--ink-dark);font-weight:400}
.leaflet--front .script-title{top:10px;font-size:50px}
.slogan{position:absolute;top:68px;left:0;width:100%;text-align:center;font-family:'Great Vibes',cursive;font-size:22px;color:var(--ink-dark)}
.fleet-intro{position:absolute;top:239px;left:30px;width:318px;text-align:center;color:var(--white);font-size:9px;line-height:1.22}
.tour-panel{position:absolute;background:var(--panel-olive)}
.leaflet--front .tour-panel{left:44px;top:295px;width:290px;height:162px}
.tour-heading{position:absolute;left:11px;top:4px;color:var(--gold);font-size:11.6px;line-height:1.1;font-weight:500}
.price-tag{position:absolute;right:0;top:3px;width:94px;height:26px;background:var(--gold-deep);color:var(--white);text-align:center}
.price-amount{font-size:14px;font-weight:600;line-height:1;padding-top:3px}
.price-amount sup{font-size:7px;vertical-align:6px}
.price-note{font-size:5.6px;line-height:1.3}
.tour-stops{position:absolute;left:11px;top:40px;width:268px;list-style:none;color:var(--white);font-size:6.2px;line-height:1.22}
.tour-stops li{margin-bottom:7.3px}
.panel-quote{position:absolute;left:0;width:100%;text-align:center;color:var(--gold);font-style:italic}
.leaflet--front .panel-quote{top:137px;font-size:8px}
.quote-mark{font-family:Georgia,serif;font-style:normal;font-weight:700;font-size:12px;line-height:0;vertical-align:-2px}
.contact-label{position:absolute;left:0;width:100%;text-align:center;color:var(--gold);font-size:5.6px;letter-spacing:1.2px}
.contact-row{position:absolute;left:46px;width:305px;display:flex;align-items:center;color:var(--white);font-weight:600}
.contact-item{display:flex;align-items:center;gap:3px}
.contact-item svg{width:7px;height:7px}
.contact-phone{font-size:7.4px}
.contact-mail,.contact-web{font-size:5.8px}
.divider{width:1px;height:8px;background:#7a7560;margin:0 10px}
.brand{position:absolute;left:0;width:100%;display:flex;justify-content:center;align-items:center;gap:5px}
.brand-dot{width:15px;height:15px;border-radius:50%;background:#b5ab8e}
.brand-name{font-size:16px;font-weight:300;color:#e8e4da}
.leaflet--front .contact-label{top:469px}
.leaflet--front .contact-row{top:479px}
.leaflet--front .brand{top:497px}
.leaflet--back .script-title{top:8px;font-size:40px;color:#2b2824}
.sights{position:absolute;list-style:none;color:var(--ink-text);font-size:8.2px;line-height:14.4px}
.sights--a{left:35px;top:58px}
.sights--b{left:136px;top:58px}
.sights--c{left:264px;top:56px}
.night-line{position:absolute;left:34px;top:111px;font-size:8.1px;font-style:italic;font-weight:700;color:var(--ink-text)}
.leaflet--back .tour-panel{left:40px;top:317px;width:306px;height:148px}
.panel-title{position:absolute;top:6px;left:0;width:100%;text-align:center;font-family:'Great Vibes',cursive;color:var(--gold);font-size:26px}
.other-tours{position:absolute;top:50px;list-style:none;color:var(--white);font-size:6.7px;line-height:14.3px;text-transform:uppercase}
.other-tours--a{left:30px}
.other-tours--b{left:170px}
.leaflet--back .panel-quote{top:109px;font-size:7px;line-height:1.25}
.leaflet--back .contact-label{top:476px}
.leaflet--back .contact-row{top:486px}
.leaflet--back .brand{top:504px}
</style>
</head>
<body>

<section class="leaflet leaflet--front">
  <div class="photo photo--castle" role="img" aria-label="Photograph of Hollenby Castle at the end of a long tree-lined avenue under a pink sunset sky"></div>
  <h1 class="script-title">Signature Tour</h1>
  <p class="slogan">Amber Coachline..Ever at your service..</p>
  <p class="fleet-intro">We have a fleet of Valtrane E, S and V Class vehicles along with 16 Seater Executive Coaches so we can accommodate single travellers, couples, friends, families and groups.</p>

  <div class="tour-panel">
    <h2 class="tour-heading">VISIT TO THE HISTORIC<br>TOWN OF WINDSOR</h2>
    <div class="price-tag">
      <div class="price-amount"><sup>$</sup>8599<sup>.00</sup></div>
      <div class="price-note">(INCLUSIVE ALL TAXES)</div>
    </div>
    <ul class="tour-stops">
      <li>Visiting the historic town of Windsor, Hollenby Castle, St Aldric’s Chapel and Regal Pemberly Shopping Arcade.</li>
      <li>Eton and Dunmere College with lovely views of the River Thames along with an array of Antique Shops in the quaint streets.</li>
      <li>Bray Village renowned for it's Brevard Star restaurants and pubs, along with a visit to Heron Isle.</li>
      <li>Through picturesque Cookham along to Marlow for some shopping in the boutique shops, small listed buildings and beautiful places for refreshments, along with stunning views of the River Thames from Ashcombe Bridge.</li>
    </ul>
    <p class="panel-quote"><span class="quote-mark">“</span> Our signature tour is approximately 4 hours <span class="quote-mark">”</span></p>
  </div>

  <p class="contact-label">CONTACT US</p>
  <div class="contact-row">
    <span class="contact-item contact-phone"><svg viewBox="0 0 10 10"><circle cx="5" cy="5" r="4.4" fill="none" stroke="#d4b84a" stroke-width=".8"/><path d="M3.5 3c.3 1.8 1.6 3.2 3.4 3.6l.4-.8-1-.5-.4.4c-.6-.3-1-.8-1.3-1.4l.4-.4-.5-1z" fill="#d4b84a"/></svg>01632 960417</span>
    <span class="divider"></span>
    <span class="contact-item contact-mail"><svg viewBox="0 0 10 10"><circle cx="5" cy="5" r="4.4" fill="none" stroke="#d4b84a" stroke-width=".8"/><rect x="2.8" y="3.5" width="4.4" height="3" fill="none" stroke="#d4b84a" stroke-width=".6"/><path d="M2.8 3.5 5 5.2l2.2-1.7" fill="none" stroke="#d4b84a" stroke-width=".6"/></svg>sales@ambercoachline.co.uk</span>
    <span class="divider"></span>
    <span class="contact-item contact-web"><svg viewBox="0 0 10 10"><circle cx="5" cy="5" r="4.4" fill="none" stroke="#d4b84a" stroke-width=".8"/><circle cx="5" cy="5" r="2.4" fill="none" stroke="#d4b84a" stroke-width=".5"/><path d="M2.6 5h4.8M5 2.6v4.8" stroke="#d4b84a" stroke-width=".5"/></svg>www.ambercoachline.co.uk</span>
  </div>
  <div class="brand"><span class="brand-dot"></span><span class="brand-name">Amber Coachline</span></div>
</section>

<section class="leaflet leaflet--back">
  <div class="photo photo--palace" role="img" aria-label="Photograph of Corringdale Palace and its memorial with red and yellow tulip beds in the foreground"></div>
  <h1 class="script-title">London Tours</h1>
  <ul class="sights sights--a"><li>Belvards</li><li>Larkmoor Park</li><li>Ravensholt Palace</li></ul>
  <ul class="sights sights--b"><li>Corringdale Palace</li><li>Pellington Square</li><li>Turning of the Sentries</li></ul>
  <ul class="sights sights--c"><li>Keep of Ardmoor</li><li>Tall Tom</li><li>Glenmoreton Abbey</li></ul>
  <p class="night-line">Or maybe London by night with a show or restaurant.</p>

  <div class="tour-panel">
    <h2 class="panel-title">Other Tours Available</h2>
    <ul class="other-tours other-tours--a"><li>Ridgewell Court Palace</li><li>Oxford and Corvane Palace</li><li>Ashmarrow Ring and Bath</li></ul>
    <ul class="other-tours other-tours--b"><li>The Cotswolds</li><li>Stratford and Penlow Castle</li><li>Quillford Shopping Village</li></ul>
    <p class="panel-quote"><span class="quote-mark">“</span> Also bespoke tours can be arranged. We can personalize any tour to <span class="quote-mark">”</span><br>your requirements with our friendly, experienced chauffeurs</p>
  </div>

  <p class="contact-label">CONTACT US</p>
  <div class="contact-row">
    <span class="contact-item contact-phone"><svg viewBox="0 0 10 10"><circle cx="5" cy="5" r="4.4" fill="none" stroke="#d4b84a" stroke-width=".8"/><path d="M3.5 3c.3 1.8 1.6 3.2 3.4 3.6l.4-.8-1-.5-.4.4c-.6-.3-1-.8-1.3-1.4l.4-.4-.5-1z" fill="#d4b84a"/></svg>01632 960417</span>
    <span class="divider"></span>
    <span class="contact-item contact-mail"><svg viewBox="0 0 10 10"><circle cx="5" cy="5" r="4.4" fill="none" stroke="#d4b84a" stroke-width=".8"/><rect x="2.8" y="3.5" width="4.4" height="3" fill="none" stroke="#d4b84a" stroke-width=".6"/><path d="M2.8 3.5 5 5.2l2.2-1.7" fill="none" stroke="#d4b84a" stroke-width=".6"/></svg>sales@ambercoachline.co.uk</span>
    <span class="divider"></span>
    <span class="contact-item contact-web"><svg viewBox="0 0 10 10"><circle cx="5" cy="5" r="4.4" fill="none" stroke="#d4b84a" stroke-width=".8"/><circle cx="5" cy="5" r="2.4" fill="none" stroke="#d4b84a" stroke-width=".5"/><path d="M2.6 5h4.8M5 2.6v4.8" stroke="#d4b84a" stroke-width=".5"/></svg>www.ambercoachline.co.uk</span>
  </div>
  <div class="brand"><span class="brand-dot"></span><span class="brand-name">Amber Coachline</span></div>
</section>

</body>
</html>
```